DJ Colm Vetter

I'm looking for a professional but still artsy/progressive design. I come from a hip hop/club DJ background playing a lot of underground music but have switched to doing more corporate parties and weddings recently. I am all about keeping the dancefloor moving and emotionally connecting with the crowd. I'd like a trendy/updated color palette. Something that's clean enough that looks professional but also trendy enough to convey that by the end of the night we'll be sweatily dancing to the latest hits. Some designers/artists I like: Tarn Olquist, Pavel Remy, Wendell Quarrie, Lumeno 7400, Silas Dravin.

```html
<!DOCTYPE html>
<html lang="en">
<head>
<meta charset="utf-8">
<title>DJ Colm Vetter — Business Card</title>
<link rel="stylesheet" href="https://fonts.googleapis.com/css2?family=Oswald:wght@400&family=Open+Sans:wght@400&display=swap">
<style>
  :root {
    --page: #2b2b2c;
    --card: #f3f2f0;
    --band: #2f2e2f;
    --ink: #1c1c1c;
    --text-light: #f4f4f4;
    --gold-light: #e9d9a0;
    --gold: #b9974f;
    --gold-dark: #8a6d33;
  }
  * { margin: 0; padding: 0; box-sizing: border-box; }
  html, body { width: 1200px; height: 800px; overflow: hidden; background: var(--page); }
  .canvas { position: relative; width: 1200px; height: 800px; }
  .card {
    position: absolute; left: 120px; top: 135px;
    width: 960px; height: 530px;
    background: var(--card);
  }
  .brand-mark {
    position: absolute; left: 50%; top: 120px;
    width: 80px; height: 80px; margin-left: -40px;
    border-radius: 50%;
    background: linear-gradient(135deg, var(--gold-light), var(--gold) 50%, var(--gold-dark));
  }
  .brand-name {
    position: absolute; left: 0; right: 0; top: 232px;
    text-align: center;
    font-family: "Oswald", sans-serif; font-weight: 400;
    font-size: 34px; letter-spacing: 0.32em;
    color: var(--ink); text-transform: uppercase;
  }
  .contact-band {
    position: absolute; left: 0; right: 0; top: 344px; height: 159px;
    background: var(--band);
  }
  .contact {
    position: absolute; display: flex; align-items: center;
    font-family: "Open Sans", sans-serif; font-size: 19px; line-height: 1.3;
    color: var(--text-light);
  }
  .contact .icon { width: 42px; height: 42px; margin-right: 18px; flex: none; }
  .contact--address { left: 140px; top: 29px; }
  .contact--email { left: 140px; top: 85px; }
  .contact--phone { left: 547px; top: 29px; }
  .contact--web { left: 547px; top: 85px; }
</style>
</head>
<body>
<div class="canvas">
  <svg width="0" height="0" style="position:absolute">
    <defs>
      <linearGradient id="gold-fill" x1="0" y1="0" x2="1" y2="1">
        <stop offset="0" stop-color="#e9d9a0"/>
        <stop offset="0.5" stop-color="#b9974f"/>
        <stop offset="1" stop-color="#8a6d33"/>
      </linearGradient>
    </defs>
  </svg>
  <div class="card">
    <div class="brand-mark" aria-hidden="true"></div>
    <div class="brand-name">DJ Colm Vetter</div>

    <div class="contact-band">
      <div class="contact contact--address">
        <svg class="icon" viewBox="0 0 42 42" aria-hidden="true">
          <circle cx="21" cy="21" r="21" fill="url(#gold-fill)"/>
          <path d="M11 21 L21 12 L31 21 L28 21 L28 30 L23.5 30 L23.5 24 L18.5 24 L18.5 30 L14 30 L14 21 Z" fill="#fff"/>
        </svg>
        <span>Street Address Here<br>Harbourview, 4471</span>
      </div>
      <div class="contact contact--email">
        <svg class="icon" viewBox="0 0 42 42" aria-hidden="true">
          <circle cx="21" cy="21" r="21" fill="url(#gold-fill)"/>
          <path d="M11 19 L31 11 L23 31 L20.5 22.5 Z" fill="#fff"/>
        </svg>
        <span>hello@colmvetter.com</span>
      </div>
      <div class="contact contact--phone">
        <svg class="icon" viewBox="0 0 42 42" aria-hidden="true">
          <circle cx="21" cy="21" r="21" fill="url(#gold-fill)"/>
          <path d="M12 17 C12 14 16 12.5 21 12.5 C26 12.5 30 14 30 17 L30 19 L26 19 L26 17 L16 17 L16 19 L12 19 Z" fill="#fff"/>
          <path d="M15 29 L17 20 L25 20 L27 29 Z" fill="#fff"/>
          <circle cx="21" cy="24.5" r="2.2" fill="#b9974f"/>
        </svg>
        <span>+18 4410 3625 0917<br>+18 4410 3625 0917</span>
      </div>
      <div class="contact contact--web">
        <svg class="icon" viewBox="0 0 42 42" aria-hidden="true">
          <circle cx="21" cy="21" r="21" fill="url(#gold-fill)"/>
          <circle cx="21" cy="21" r="9" fill="none" stroke="#fff" stroke-width="2"/>
          <ellipse cx="21" cy="21" rx="4" ry="9" fill="none" stroke="#fff" stroke-width="1.6"/>
          <line x1="12" y1="21" x2="30" y2="21" stroke="#fff" stroke-width="1.6"/>
        </svg>
        <span>www.colmvetter.com</span>
      </div>
    </div>
  </div>
</div>
</body>
</html>
```